Redesign This Psychology Website

We would like a slight redesign of this successful psychology (relationship counselling) website:

www.TheKelvaleClinic.com.au

We are updating the website, and we'd like a slight refresh of the design and style.

Please keep to very similar colours, and use the same logo. We're looking for around 10 page templates, however the main one is the home page.

Keep in mind, this website already converts quite well, so we want a new, fresh design in keeping with this one. Please don't bother designing something too extremely different.

thanks :)

Target Market(s)

couples who are looking for relationship counselling. Men and women, 25 - 70, across Australia

Industry/Entity Type

Psychology

Number of Pages Required

5+ page

Font styles to use
Sans Serif

Colors
87cfc6
b7a5cd
ec1f27
ffffff
cee9f5

Requirements
Must have
• a similar look to the current design, just looking for a slight refresh.
• Search bar
• Areas for lots of photos
• same logo
• lots of content areas
Nice to have
• great content areas, where we can display a lot of content and our areas.
Should not have
• no colors like orange, etc.
• should not have a totally different feel.

```html
<!DOCTYPE html>
<html lang="en">
<head>
<meta charset="utf-8">
<title>FAQ – The Kelvale Clinic</title>
<link rel="stylesheet" href="https://fonts.googleapis.com/css2?family=Mulish:wght@400;500;600;700&family=Open+Sans:wght@400;600&display=swap">
<style>
:root{
  --teal:#87cfc6;
  --teal-dark:#0f7d89;
  --brand:#1d7f8e;
  --lilac:#b7a5cd;
  --lilac-btn:#a58fc4;
  --red:#ec1f27;
  --white:#ffffff;
  --ink:#333333;
  --grey:#6f6f6f;
  --top:#f2f2f2;
}
*{box-sizing:border-box;margin:0;padding:0}
html,body{width:1200px;height:2230px;overflow:hidden;background:var(--white)}
body{position:relative;font-family:"Open Sans",Arial,sans-serif;color:var(--ink)}

.topbar{position:absolute;left:0;top:0;width:1200px;height:36px;background:var(--top);border-bottom:1px solid #e2e2e2}
.topbar .associate{position:absolute;left:146px;top:9px;font-size:14px;color:#555}
.topbar .links{position:absolute;right:132px;top:0;display:flex;height:36px}
.topbar .links span{padding:0 13px;line-height:36px;font-size:13px;color:#666;border-left:1px solid #ddd}

.header{position:absolute;left:0;top:36px;width:1200px;height:124px}
.brand{position:absolute;left:131px;top:30px;display:flex;align-items:center;gap:12px}
.brand-dot{width:54px;height:54px;border-radius:50%;background:var(--brand)}
.brand-name{font-family:"Mulish",sans-serif;font-size:30px;font-weight:500;color:var(--brand);line-height:1}
.search{position:absolute;left:471px;top:47px;width:356px;height:39px;border:1px solid #d4d4d4;border-radius:3px;display:flex;align-items:center;padding-left:12px;gap:8px;font-size:13px;color:#999}
.callus{position:absolute;right:132px;top:40px;text-align:right}
.callus .label{font-family:"Mulish",sans-serif;font-size:17px;color:var(--teal)}
.callus .number{font-family:"Mulish",sans-serif;font-size:24px;font-weight:600;color:var(--brand);display:flex;align-items:center;gap:6px}

.nav{position:absolute;left:0;top:160px;width:1200px;height:68px;background:linear-gradient(#9fd9d1,#75c5ba)}
.nav ul{list-style:none;display:flex;position:absolute;left:131px;top:0;height:68px}
.nav li{display:flex;align-items:center;justify-content:center;text-align:center;color:var(--white);font-family:"Mulish",sans-serif;font-weight:600;font-size:16px;line-height:17px;border-right:1px solid rgba(255,255,255,.45);padding:0 10px}
.nav li:last-child{border-right:none}

.hero{position:absolute;left:0;top:228px;width:1200px;height:325px;background:linear-gradient(100deg,#7d6a5a 0%,#b39a82 30%,#c8b6a4 55%,#8c735f 80%,#6e5a4a 100%)}
.hero h1{position:absolute;left:126px;top:170px;font-family:"Mulish",sans-serif;font-size:36px;font-weight:700;color:var(--white)}

.faq{position:absolute;left:131px;top:608px;width:607px}
.faq h2{font-family:"Mulish",sans-serif;font-weight:400;font-size:29px;color:#333;margin-left:4px;height:76px}
.faq-item{height:46px;background:var(--teal);border-bottom:2px solid var(--white);display:flex;align-items:center;justify-content:space-between;padding:0 18px 0 32px;color:var(--white);font-size:14px}
.faq-item.open{background:var(--teal-dark);height:43px;border-bottom:none;font-size:16px;padding-left:24px}
.faq-body{border:1px solid #cfcfcf;border-top:none;padding:24px 26px 26px 26px;font-size:12.6px;line-height:22px;color:var(--grey);height:403px}
.faq-body .strong{font-weight:600;color:#555}
.faq-body p{margin-bottom:9px}

.finder{position:absolute;left:767px;top:599px;width:301px;height:364px;background:var(--lilac);padding:24px 16px}
.finder h3{font-family:"Mulish",sans-serif;font-weight:600;color:var(--white);font-size:24px;text-align:center;line-height:30px}
.finder label{display:block;color:var(--white);font-size:14px;line-height:18px;margin:14px 0 4px 4px}
.finder .field{height:31px;background:var(--white);border-radius:2px;font-size:11px;color:#888;display:flex;align-items:center;justify-content:space-between;padding:0 12px}
.finder .go{margin-top:16px;height:38px;background:var(--red);color:var(--white);font-family:"Mulish",sans-serif;font-weight:600;font-size:17px;display:flex;align-items:center;justify-content:center}

.promo{position:absolute;left:763px;width:306px;height:237px;border:1px solid #e0e0e0;box-shadow:0 1px 4px rgba(0,0,0,.12);background:var(--white);overflow:hidden}
.promo h4{position:absolute;left:24px;top:24px;font-family:"Mulish",sans-serif;font-weight:600;font-size:20px;line-height:25px;color:#222}
.promo p{position:absolute;left:24px;top:82px;width:140px;font-size:11px;line-height:19px;color:#666}
.promo .more{position:absolute;left:24px;top:174px;width:95px;height:26px;background:var(--lilac-btn);color:var(--white);font-size:10px;font-weight:600;display:flex;align-items:center;justify-content:center}
.promo .photo{position:absolute;right:0;top:0;width:142px;height:100%;clip-path:polygon(22% 0,100% 0,100% 100%,0 100%)}

.footer{position:absolute;left:0;top:1859px;width:1200px;height:297px;background:linear-gradient(#ececec,#fafafa 40%,#fafafa)}
.footer .brand{left:152px;top:78px}
.fcol{position:absolute;top:62px;font-size:13px;color:#555;line-height:27px}
.fcol h5{font-family:"Mulish",sans-serif;font-size:17px;font-weight:600;color:var(--brand);margin-bottom:8px;line-height:20px}
.social{display:flex;gap:7px;margin-top:10px}
.social span{width:32px;height:32px;border-radius:50%}
.bottombar{position:absolute;left:12px;top:2156px;width:1188px;height:74px;background:#f0f0f0;text-align:center;font-size:12px;color:#666;line-height:74px}
</style>
</head>
<body>
<div class="topbar">
  <div class="associate">Join Our Assoicate Program →</div>
  <div class="links"><span>Home</span><span>Cart</span><span>Blog</span><span>Resources</span><span>Contact</span></div>
</div>

<header class="header">
  <div class="brand"><div class="brand-dot"></div><div class="brand-name">The Kelvale Clinic</div></div>
  <div class="search"><svg width="16" height="16" viewBox="0 0 16 16"><circle cx="6.5" cy="6.5" r="5" fill="none" stroke="#aaa" stroke-width="1.6"/><line x1="10.3" y1="10.3" x2="15" y2="15" stroke="#aaa" stroke-width="1.6"/></svg>Search here</div>
  <div class="callus"><div class="label">Call Us Now</div><div class="number"><svg width="22" height="22" viewBox="0 0 24 24"><path d="M6.6 10.8c1.4 2.8 3.8 5.1 6.6 6.6l2.2-2.2c.3-.3.7-.4 1-.2 1.1.4 2.3.6 3.6.6.6 0 1 .4 1 1V20c0 .6-.4 1-1 1C10.6 21 3 13.4 3 4c0-.6.4-1 1-1h3.5c.6 0 1 .4 1 1 0 1.3.2 2.5.6 3.6.1.3 0 .7-.2 1z" fill="none" stroke="#ec1f27" stroke-width="1.6"/></svg>1300 555 014</div></div>
</header>

<nav class="nav"><ul>
  <li style="width:139px">COUNSELLING<br>TYPES</li>
  <li style="width:264px">RELATIONSHIP COUNSELLING<br>LOCATIONS</li>
  <li style="width:136px">SEX THERAPY<br>LOCATIONS</li>
  <li style="width:112px">ABOUT US</li>
  <li style="width:100px">QUIZZES</li>
  <li style="width:98px">FAQ'S</li>
  <li style="width:88px">CONTACT</li>
</ul></nav>

<section class="hero" role="img" aria-label="Photo of a smiling couple lying on a wooden floor with a laptop"><h1>FAQ</h1></section>

<main class="faq">
  <h2>FAQs about our Relationship Counselling</h2>
  <div class="faq-item open">What are the fees involved, and are there any rebates?<svg width="18" height="12" viewBox="0 0 18 12"><polyline points="2,10 9,3 16,10" fill="none" stroke="#fff" stroke-width="2.4"/></svg></div>
  <div class="faq-body">
    <p class="strong" style="margin-bottom:2px">Couples Counselling and Maarriage counselling sessions are 50 mins</p>
    <p class="strong">Cost: $160 &nbsp;($175 for after hours sessions or for all sessions in CBD locations)</p>
    <p>Private health rebates should apply if you have 'psychology' as an extra, but we recommend that you call your fund and check your level of cover if this is of concern to you. &nbsp;Unfortunately funds don't give us these details.</p>
    <p>Medicare rebates may also apply if you are suffering anxiety, depression etc, and you are successful in applying for a Mental Health Care Plan with your doctor. &nbsp;These plans are not provided for relationship counselling as such, but you may be able to use them for appointments when you are in attendance on your own. &nbsp;It is quite common to attend some sessions on your own whilst undergoing relationship counselling. &nbsp;You may be able to use them with your partner in attendance for some appointments, but this would be up to each individual psychologist to determine once they have seen you for the first time and sighted your plan. Please contact your doctor or GP to determine your eligibility for a Mental Health Care Plan. The Medicare rebate is $84.80.</p>
  </div>
  <div class="faq-item">What happens in a marriage/relationship counselling session?<svg width="18" height="12" viewBox="0 0 18 12"><polyline points="2,3 9,10 16,3" fill="none" stroke="#fff" stroke-width="2.4"/></svg></div>
  <div class="faq-item">How helpful will it be?<svg width="18" height="12" viewBox="0 0 18 12"><polyline points="2,3 9,10 16,3" fill="none" stroke="#fff" stroke-width="2.4"/></svg></div>
  <div class="faq-item">Are we too late for relationship counselling?<svg width="18" height="12" viewBox="0 0 18 12"><polyline points="2,3 9,10 16,3" fill="none" stroke="#fff" stroke-width="2.4"/></svg></div>
  <div class="faq-item">Can we hope for any real lasting changes?<svg width="18" height="12" viewBox="0 0 18 12"><polyline points="2,3 9,10 16,3" fill="none" stroke="#fff" stroke-width="2.4"/></svg></div>
  <div class="faq-item">Do you take sides?<svg width="18" height="12" viewBox="0 0 18 12"><polyline points="2,3 9,10 16,3" fill="none" stroke="#fff" stroke-width="2.4"/></svg></div>
  <div class="faq-item">Do you support relationships or individuals first?<svg width="18" height="12" viewBox="0 0 18 12"><polyline points="2,3 9,10 16,3" fill="none" stroke="#fff" stroke-width="2.4"/></svg></div>
  <div class="faq-item">(For men) Will the girls gang up on me?<svg width="18" height="12" viewBox="0 0 18 12"><polyline points="2,3 9,10 16,3" fill="none" stroke="#fff" stroke-width="2.4"/></svg></div>
  <div class="faq-item">Should we first come to sessions together or on our own?<svg width="18" height="12" viewBox="0 0 18 12"><polyline points="2,3 9,10 16,3" fill="none" stroke="#fff" stroke-width="2.4"/></svg></div>
  <div class="faq-item">What do I do if my partner doesn't want to come?<svg width="18" height="12" viewBox="0 0 18 12"><polyline points="2,3 9,10 16,3" fill="none" stroke="#fff" stroke-width="2.4"/></svg></div>
  <div class="faq-item">Can I come on my own without my partner knowing?<svg width="18" height="12" viewBox="0 0 18 12"><polyline points="2,3 9,10 16,3" fill="none" stroke="#fff" stroke-width="2.4"/></svg></div>
  <div class="faq-item">How do I prepare for the first session?<svg width="18" height="12" viewBox="0 0 18 12"><polyline points="2,3 9,10 16,3" fill="none" stroke="#fff" stroke-width="2.4"/></svg></div>
  <div class="faq-item">What if it doesn't work?<svg width="18" height="12" viewBox="0 0 18 12"><polyline points="2,3 9,10 16,3" fill="none" stroke="#fff" stroke-width="2.4"/></svg></div>
  <div class="faq-item">What if I cancel?<svg width="18" height="12" viewBox="0 0 18 12"><polyline points="2,3 9,10 16,3" fill="none" stroke="#fff" stroke-width="2.4"/></svg></div>
  <div class="faq-item">Would VIDEO counselling be suitable for us or me?<svg width="18" height="12" viewBox="0 0 18 12"><polyline points="2,3 9,10 16,3" fill="none" stroke="#fff" stroke-width="2.4"/></svg></div>
</main>

<aside class="finder">
  <h3>Find Our Psychologist<br>— Near You —</h3>
  <label>Type of Counselling</label>
  <div class="field">Select<svg width="12" height="8" viewBox="0 0 12 8"><polyline points="1,1 6,6 11,1" fill="none" stroke="#777" stroke-width="1.4"/></svg></div>
  <label>Location</label>
  <div class="field"></div>
  <label>Postcode</label>
  <div class="field"></div>
  <div class="go">SEARCH</div>
</aside>

<div class="promo" style="top:980px">
  <h4>Rebates<br>Available</h4>
  <p>Maecenas aliquet velit vel turpis Mauris neque metus malesuada nec ultricies sit amet</p>
  <div class="more">Learn More</div>
  <div class="photo" role="img" aria-label="Photo of two hands reaching toward each other against a sunset" style="background:linear-gradient(#f3c9c8,#f2a04f 60%,#e07a1e)"></div>
</div>
<div class="promo" style="top:1239px">
  <h4>GP Referral<br>Info</h4>
  <p>Maecenas aliquet velit vel turpis Mauris neque metus malesuada nec ultricies sit amet</p>
  <div class="more">Learn More</div>
  <div class="photo" role="img" aria-label="Photo of a doctor in a white coat with a stethoscope" style="background:linear-gradient(#f4f4f4,#e3e6e8)"></div>
</div>
<div class="promo" style="top:1497px">
  <h4>Anxiety and<br>Depression</h4>
  <p>Maecenas aliquet velit vel turpis Mauris neque metus malesuada nec ultricies sit amet</p>
  <div class="more">Learn More</div>
  <div class="photo" role="img" aria-label="Photo of a worried man resting his head in his hand" style="background:linear-gradient(135deg,#3c4a4c,#1f2829)"></div>
</div>

<footer class="footer">
  <div class="brand"><div class="brand-dot"></div><div class="brand-name">The Kelvale Clinic</div></div>
  <div class="fcol" style="left:474px"><h5>QUICK LINKS</h5>Home<br>About Us<br>Our Blogs<br>Shop Cart<br>Contact Us</div>
  <div class="fcol" style="left:642px"><h5>RESOURCES</h5>Counselling Type<br>Sex Therapy<br>Quizzes<br>FAQ<br>Relationship Counselling</div>
  <div class="fcol" style="left:846px"><h5>CONTACT US</h5>42 Harbour Lane Suite 12<br>1300 555 014<br>Email: info@kelvaleclinic.com.au
    <div class="social"><span style="background:#5aaedf"></span><span style="background:#2d5a9a"></span><span style="background:#1a7bb1"></span><span style="background:#d8452f"></span></div>
  </div>
</footer>
<div class="bottombar">© 2017 Company Name &nbsp;All right reserved</div>
</body>
</html>
```